Zielgruppe
Immobilienmakler
Aufgabenstellung
Top moderne hochwertige Visitenkate, wir hätten gerne eine sehr hochwertig moderne Visitenkarte mit Bild vom Mitarbeiter... Anbei habe ich die alte Visitenkarte die ich sehr kindlich finde... Es sollte jetzt sehr exklusive aussehen. Alle Daten können von der alten Visitenkarte übernommen werden.. danke

```html
<!DOCTYPE html>
<html lang="de">
<head>
<meta charset="utf-8">
<title>Velta Agentur – Visitenkarte</title>
<link rel="stylesheet" href="https://fonts.googleapis.com/css2?family=Noto+Serif:wght@400;700&display=swap">
<style>
  :root {
    --backdrop: #c8c8ca;
    --card-dark: #15171b;
    --card-light: #f6f6f8;
    --brand-green: #0d8a44;
    --ink: #1b1b1b;
    --stripe: #111111;
    --photo-tone: #dfe3e8;
    --sage: #c9d5c9;
    --sage-light: #dde6dd;
    --white: #ffffff;
  }
  * { margin: 0; padding: 0; box-sizing: border-box; }
  html, body { width: 1200px; height: 786px; overflow: hidden; background: var(--backdrop); }
  body { font-family: "Noto Serif", Georgia, serif; color: var(--ink); position: relative; }

  .card {
    position: absolute;
    top: 225px;
    width: 520px;
    height: 336px;
    overflow: hidden;
    box-shadow: 0 6px 18px rgba(0,0,0,0.18);
  }

  /* Front */
  .card-front { left: 50px; background: var(--card-dark); display: flex; flex-direction: column; align-items: center; justify-content: center; }
  .brand-name { color: var(--white); font-weight: 700; font-size: 40px; letter-spacing: 0.5px; line-height: 1; }
  .brand-tagline { color: var(--white); font-size: 11px; letter-spacing: 1.5px; text-transform: uppercase; margin-top: 8px; }

  /* Back */
  .card-back { left: 630px; background: var(--card-light); }
  .green-band { position: absolute; left: 0; top: 0; width: 104px; height: 100%; background: var(--brand-green); }
  .black-stripe { position: absolute; left: 108px; top: 0; width: 4px; height: 100%; background: var(--stripe); }
  .staff-photo {
    position: absolute; left: 70px; top: 22px; width: 76px; height: 76px; border-radius: 50%;
    background: radial-gradient(circle at 50% 40%, #f3f3f5 0%, var(--photo-tone) 60%, #c4ccd8 100%);
    border: 3px solid var(--card-light);
  }
  .person { position: absolute; left: 166px; top: 44px; right: 0; }
  .person-name { color: var(--brand-green); font-weight: 700; font-size: 20px; letter-spacing: 0.5px; line-height: 1.1; }
  .person-role { font-size: 11.5px; margin-top: 2px; }
  .rule { height: 2px; background: var(--brand-green); margin-top: 4px; }
  .person-mail { display: flex; align-items: center; gap: 8px; font-size: 11.5px; margin-top: 6px; }
  .person-mail svg { width: 13px; height: 9px; flex: none; }

  .company { position: absolute; left: 158px; top: 158px; font-size: 12.5px; line-height: 1.25; }
  .company-name { font-weight: 700; }
  .contact-lines { position: absolute; left: 158px; top: 210px; font-size: 12.5px; line-height: 1.3; }
  .contact-lines b { display: inline-block; width: 36px; }
  .web-lines { position: absolute; left: 158px; top: 256px; font-size: 12.5px; line-height: 1.3; }

  .seal {
    position: absolute; left: 392px; top: 223px; width: 104px; height: 104px; border-radius: 50%;
    background: var(--sage);
  }
  .seal::after {
    content: ""; position: absolute; inset: 18px; border-radius: 50%; background: var(--sage-light);
  }
</style>
</head>
<body>
  <section class="card card-front">
    <div class="brand-name">Velta Agentur</div>
    <div class="brand-tagline">Der Immobilienmakler</div>
  </section>

  <section class="card card-back">
    <div class="green-band"></div>
    <div class="black-stripe"></div>
    <div class="staff-photo" role="img" aria-label="Porträtfoto des Mitarbeiters"></div>

    <div class="person">
      <div class="person-name">LUKAS BRENNER</div>
      <div class="person-role">Dipl. Immobilienmanager / Geschäftsführer</div>
      <div class="rule"></div>
      <div class="person-mail">
        <svg viewBox="0 0 13 9" aria-hidden="true"><rect width="13" height="9" fill="#0d8a44"/><path d="M0.5 0.8 L6.5 5 L12.5 0.8" stroke="#fff" stroke-width="1.2" fill="none"/></svg>
        lukas@velta-agentur.com
      </div>
    </div>

    <div class="company">
      <div class="company-name">Velta-Agentur Brenner GmbH</div>
      <div>Lindenweg 4 • AT - 6900 Bregenz</div>
    </div>

    <div class="contact-lines">
      <div><b>Fon</b>+43 5574 48 210 20</div>
      <div><b>Fax</b>+43 664 3071 482</div>
    </div>

    <div class="web-lines">
      <div>office@velta-agentur.com</div>
      <div>www.velta-agentur.com</div>
    </div>

    <div class="seal" aria-hidden="true"></div>
  </section>
</body>
</html>
```